Business card design for new eCommerce site focusing on integrity and strong businsess tactics

We need a business card that will stand out and be memorable. Something with color that matches our company logo colors. Think high end version of Pactivo. There are 2 logos provided. The parent company is called Amber Ledge Partners and we are presenting a new and very exciting eCommerce site called BrightHarborTrade.example.

Target Market(s)

Our target markets are in the Activities, Food and Beverage, Health and Beauty

Industry/Entity Type

Marketing

Contact Information for Business Card

We have 4 members that need cards...I will provide all info to the winner of the design contest
Business Address is
4870 West 63rd Avenue, Suite C207
Phoenix AZ 85731

Font styles to use
Serif
Sans Serif

Colors

Designer to choose colors to be used in the design.

Requirements
Must have
• The card must be memorable...should be unique in design but must exude integrity and be playful .
• I have provided several colors or our parent company...please feel free to use which ever
Nice to have
• I will leave this up to you. Feel free to use other images of your choosing that wraps around our client.....Activities, Dining, Health, Beauty
Should not have
• just dont be boring

```html
<!DOCTYPE html>
<html lang="en">
<head>
<meta charset="utf-8">
<title>BrightHarborTrade.example – Business Card</title>
<link rel="stylesheet" href="https://fonts.googleapis.com/css2?family=Questrial&family=Jost:wght@400;500;600&family=Arimo:wght@700&display=swap">
<style>
  :root {
    --stage: #2b2b2b;
    --card-white: #f7f7f7;
    --brand-green: #8cc540;
    --back-green: #a9cc47;
    --brand-blue: #2e7db5;
    --back-blue-light: #42bcd8;
    --back-blue-deep: #2c7ab0;
    --text-grey: #555555;
    --white: #ffffff;
  }
  * { margin: 0; padding: 0; box-sizing: border-box; }
  html, body { width: 1200px; height: 960px; overflow: hidden; }
  body { background: var(--stage); position: relative; font-family: "Jost", sans-serif; }

  .card { position: absolute; width: 600px; height: 342px; border-radius: 18px; overflow: hidden; }

  .card-front { left: 302px; top: 131px; background: var(--card-white); }

  .brand { position: absolute; left: 24px; top: 66px; display: flex; align-items: center; gap: 12px; }
  .brand-dot { width: 34px; height: 34px; border-radius: 50%; background: var(--brand-green); flex: none; }
  .brand-name { font-family: "Questrial", sans-serif; font-size: 26px; color: var(--brand-green); line-height: 1; }

  .address { position: absolute; left: 48px; top: 162px; font-size: 15px; line-height: 18px; color: var(--text-grey); }
  .contact-list { position: absolute; left: 48px; top: 226px; list-style: none; font-size: 15px; line-height: 19.3px; color: var(--text-grey); }
  .contact-list li { display: flex; align-items: center; gap: 8px; }
  .contact-list svg { width: 14px; height: 14px; fill: var(--brand-blue); flex: none; }

  .name-tag { position: absolute; left: 397px; top: 203px; width: 203px; height: 67px; background: var(--brand-blue); border-left: 5px solid var(--brand-green); box-shadow: inset 3px 0 0 var(--white); color: var(--white); text-align: center; padding-top: 12px; padding-left: 8px; }
  .person-name { font-size: 22px; font-weight: 600; line-height: 1.05; letter-spacing: 0.2px; white-space: nowrap; }
  .person-role { font-size: 14px; font-weight: 400; line-height: 1.2; }

  .card-back { left: 299px; top: 490px; background: linear-gradient(135deg, var(--back-blue-light) 0%, var(--back-blue-deep) 45%, var(--back-blue-deep) 100%); }
  .parent-mark { position: absolute; left: 226px; top: 70px; width: 148px; height: 148px; border-radius: 50%; background: var(--back-green); box-shadow: 0 0 0 2px var(--back-blue-deep), 0 0 0 4px var(--back-green); }
  .parent-name { position: absolute; left: 0; right: 0; top: 222px; text-align: center; font-family: "Arimo", sans-serif; font-weight: 700; font-size: 34px; color: var(--back-green); }
</style>
</head>
<body>
  <section class="card card-front">
    <div class="brand">
      <span class="brand-dot"></span>
      <span class="brand-name">BrightHarborTrade.example</span>
    </div>

    <p class="address">4870 West 63rd Avenue<br>Suite C207<br>Phoenix AZ 85731</p>

    <ul class="contact-list">
      <li><svg viewBox="0 0 24 24"><path d="M6.6 10.8a15 15 0 0 0 6.6 6.6l2.2-2.2a1 1 0 0 1 1-.25 11.4 11.4 0 0 0 3.6.57 1 1 0 0 1 1 1V20a1 1 0 0 1-1 1A17 17 0 0 1 3 4a1 1 0 0 1 1-1h3.5a1 1 0 0 1 1 1c0 1.250.2 2.450.57 3.570a1 1 0 0 1-.25 1z"/></svg>555 210 4836</li>
      <li><svg viewBox="0 0 24 24"><path d="M7 1h10a2 2 0 0 1 2 2v18a2 2 0 0 1-2 2H7a2 2 0 0 1-2-2V3a2 2 0 0 1 2-2zm0 3v14h10V4zm5 15.5a1 1 0 1 0 0 2 1 1 0 0 0 0-2z"/></svg>555 397 1802</li>
      <li><svg viewBox="0 0 24 24"><path d="M2 5h20v14H2zm2 2v.5l8 5 8-5V7l-8 5z"/></svg>dana@brightharbortrade.example</li>
      <li><svg viewBox="0 0 24 24"><path d="M12 2a10 10 0 1 0 0 20 10 10 0 0 0 0-20zm-1 17.9A8 8 0 0 1 4.1 11H7v2l3 3v3.9zM17.9 16.4A2 2 0 0 0 16 15h-1v-3H9v-2h2V8h2V5.4a8 8 0 0 1 4.9 11z"/></svg>www.brightharbortrade.example</li>
    </ul>

    <div class="name-tag">
      <p class="person-name">DANA KERR</p>
      <p class="person-role">CEO/FOUNDER</p>
    </div>
  </section>

  <section class="card card-back">
    <span class="parent-mark"></span>
    <p class="parent-name">Amber Ledge Partners</p>
  </section>
</body>
</html>
```